A website for Kovadrel Limited

We need a new and modern website for our company. We are engineering consultants and contractors (EPC) in the oil and gas industry and building services industry.
What we do:
Engineering, procurement, construction
Automation (safety and process)
Non-destructive testing
Training
We have an existing website and the content can be referred from there since we are remaking the website
For more information visit Kovadrel Limited Kenya

```html
<!DOCTYPE html>
<html lang="en">
<head>
<meta charset="utf-8">
<title>Kovadrel Limited</title>
<link href="https://fonts.googleapis.com/css2?family=Antonio:wght@300;400&family=Raleway:wght@400;500;600;700&display=swap" rel="stylesheet">
<style>
:root{
  --orange:#d9532f;
  --orange-soft:#e8714a;
  --yellow:#f2b15f;
  --ink:#2b2b2b;
  --muted:#4a4a4a;
  --grey-bg:#f5f5f6;
  --white:#ffffff;
}
*{margin:0;padding:0;box-sizing:border-box}
html,body{width:1200px;height:3516px;overflow:hidden}
body{position:relative;background:var(--white);font-family:"Raleway",sans-serif;color:var(--ink)}
.abs{position:absolute}
.brand{display:flex;align-items:center;gap:10px;color:var(--orange);font-family:"Raleway",sans-serif;font-weight:500;font-size:19px;line-height:1.1}
.brand-dot{width:56px;height:56px;border-radius:50%;background:var(--orange)}
.nav{position:absolute;top:48px;left:388px;display:flex;gap:32px;font-size:17px;color:var(--ink)}
.nav .active{color:var(--orange)}
.hero-title{font-family:"Antonio",sans-serif;font-weight:300;font-size:66px;line-height:70px;color:#1b1b1b;letter-spacing:-1px}
.btn{display:flex;align-items:center;justify-content:center;color:#fff;background:var(--orange);font-size:17px;clip-path:polygon(8% 0,100% 0,92% 100%,0 100%)}
.section-title{position:absolute;left:0;width:1200px;text-align:center;font-family:"Antonio",sans-serif;font-weight:300;font-size:42px;color:#1b1b1b}
.service{position:absolute;width:262px}
.service .shape{position:absolute;inset:0}
.service .label{position:absolute;left:0;right:0;text-align:center;color:#fff;font-weight:700;font-size:16px;line-height:18px}
.arrow-box{position:absolute;width:48px;height:46px;background:var(--yellow);display:flex;align-items:center;justify-content:center}
.about-card{position:absolute;left:67px;top:1308px;width:609px;height:372px;background:#f4f4f6;box-shadow:0 6px 18px rgba(0,0,0,.12)}
.about-card h2{position:absolute;left:44px;top:34px;font-family:"Antonio",sans-serif;font-weight:300;font-size:40px;color:#1b1b1b}
.about-card p{position:absolute;left:44px;top:98px;width:480px;font-size:17px;line-height:29px;color:var(--muted)}
.project-frame{position:absolute;width:322px;height:257px;border:1px solid var(--orange)}
.project-img{position:absolute;width:290px;height:291px}
.project-img span{position:absolute;left:0;right:0;text-align:center;color:#fff;font-weight:700;font-size:16px;line-height:29px}
.partner{position:absolute;top:2670px;width:90px;height:90px;border-radius:50%}
.contact{position:absolute;top:3187px;left:0;width:1200px;height:171px;background:var(--grey-bg)}
.c-icon{position:absolute;top:56px;width:34px;height:38px;background:var(--orange);border-radius:4px;display:flex;align-items:center;justify-content:center}
.c-text{position:absolute;font-size:15px;line-height:29px;color:var(--muted)}
.foot-nav{position:absolute;top:3392px;left:0;width:1200px;display:flex;justify-content:center;gap:32px;font-size:17px;color:var(--ink)}
.rule{position:absolute;top:3440px;left:0;width:1200px;height:1px;background:#d8d8d8}
.copy{position:absolute;top:3468px;left:0;width:1200px;text-align:center;font-size:14px;color:var(--muted)}
</style>
</head>
<body>

<header>
  <div class="brand abs" style="left:107px;top:30px"><span class="brand-dot"></span><span>Kovadrel<br>Limited</span></div>
  <nav class="nav"><span class="active">Home</span><span>About Us</span><span>Our Clients</span><span>Our Partners</span><span>Where We Operate</span><span>Contact Us</span></nav>
</header>

<section class="hero">
  <svg class="abs" style="left:0;top:115px" width="1200" height="565" viewBox="0 0 1200 565">
    <defs>
      <linearGradient id="heroGrad" x1="0" y1="0" x2="1" y2="0">
        <stop offset="0" stop-color="#f3c9b8"/><stop offset=".4" stop-color="#c98a9a"/><stop offset=".7" stop-color="#6f7fb0"/><stop offset="1" stop-color="#2a6db0"/>
      </linearGradient>
    </defs>
    <polygon role="img" aria-label="Worker in a hard hat before an oil refinery" points="0,0 1200,0 1200,472 600,515 0,472" fill="url(#heroGrad)"/>
    <polygon points="0,472 600,515 1200,472 1200,484 600,561 0,484" fill="var(--orange)"/>
    <circle cx="581" cy="499" r="6" fill="var(--orange)"/><circle cx="600" cy="499" r="6" fill="#fff"/><circle cx="619" cy="499" r="6" fill="#fff"/>
  </svg>
  <h1 class="hero-title abs" style="left:110px;top:258px">WELCOME TO<br>KOVADREL LIMITED</h1>
  <div class="btn abs" style="left:110px;top:414px;width:174px;height:43px">Get Started</div>
</section>

<section class="services">
  <h2 class="section-title" style="top:726px">WHAT WE DO</h2>
  <div class="service" style="left:35px;top:765px;height:275px">
    <div class="shape" role="img" aria-label="Excavator on a construction site" style="background:linear-gradient(160deg,#e98a5a,#b8482c);clip-path:polygon(0 0,100% 10%,100% 100%,0 92%)"></div>
    <div class="label" style="top:183px">ENGINEERING,<br>PROCUREMENT, CONSTRUCTION</div>
    <div class="arrow-box" style="left:107px;top:228px"><svg width="14" height="14" viewBox="0 0 14 14"><path d="M5 2l5 5-5 5" stroke="#222" stroke-width="2" fill="none"/></svg></div>
  </div>
  <div class="service" style="left:319px;top:808px;height:276px">
    <div class="shape" role="img" aria-label="Technician working on process controls" style="background:linear-gradient(160deg,#d98a78,#e0a07a);clip-path:polygon(0 0,100% 10%,100% 100%,0 92%)"></div>
    <div class="label" style="top:182px">AUTOMATION<br>(SAFETY AND PROCESS)</div>
    <div class="arrow-box" style="left:107px;top:235px"><svg width="14" height="14" viewBox="0 0 14 14"><path d="M5 2l5 5-5 5" stroke="#222" stroke-width="2" fill="none"/></svg></div>
  </div>
  <div class="service" style="left:627px;top:822px;height:277px">
    <div class="shape" role="img" aria-label="Handheld ultrasonic testing device" style="background:linear-gradient(160deg,#a9483a,#d5704e);clip-path:polygon(0 10%,100% 0,100% 92%,0 100%)"></div>
    <div class="label" style="top:184px">NON-DESTRUCTIVE TESTING</div>
    <div class="arrow-box" style="left:107px;top:235px"><svg width="14" height="14" viewBox="0 0 14 14"><path d="M5 2l5 5-5 5" stroke="#222" stroke-width="2" fill="none"/></svg></div>
  </div>
  <div class="service" style="left:912px;top:779px;height:276px">
    <div class="shape" role="img" aria-label="Laboratory flask with amber liquid" style="background:linear-gradient(160deg,#e89a88,#e4a052);clip-path:polygon(0 10%,100% 0,100% 92%,0 100%)"></div>
    <div class="label" style="top:183px">TRAINING</div>
    <div class="arrow-box" style="left:107px;top:233px"><svg width="14" height="14" viewBox="0 0 14 14"><path d="M5 2l5 5-5 5" stroke="#222" stroke-width="2" fill="none"/></svg></div>
  </div>
</section>

<section class="about">
  <svg class="abs" style="left:0;top:1103px" width="1200" height="683" viewBox="0 0 1200 683">
    <rect x="0" y="0" width="1200" height="683" fill="var(--grey-bg)"/>
    <polygon points="0,0 1200,0 1200,45 600,55 0,45" fill="#fff"/>
    <polygon points="0,0 600,55 1200,0 1200,12 600,90 0,12" fill="var(--orange)"/>
  </svg>
  <div class="about-card">
    <h2>ABOUT US</h2>
    <p>Lorem ipsum dolor sit amet, consectetur adipiscing elit, sed do eiusmod tempor incididunt ut labore et dolore magna aliqua. Quis ipsum suspendisse ultrices gravida. Risus commodo viverra maecenas accumsan lacus vel facilisis. Quis ipsum suspendisse ultrices gravida. Risus commodo viverra maecenas accumsan lacus vel facilisis.</p>
    <div class="btn abs" style="left:34px;top:300px;width:174px;height:43px">Read More</div>
  </div>
  <div class="abs" style="left:645px;top:1298px;width:489px;height:336px;border:1px solid var(--orange)"></div>
  <div class="abs" role="img" aria-label="Engineer with a tablet beside red pipeline valves" style="left:627px;top:1280px;width:490px;height:338px;background:linear-gradient(110deg,#b9483e 0%,#8a8f96 40%,#2f3f6e 75%,#d8c24a 100%)"></div>
</section>

<section class="projects">
  <h2 class="section-title" style="top:1858px">OUR PROJECT</h2>
  <div class="project-frame" style="left:67px;top:1971px"></div>
  <div class="project-img" role="img" aria-label="Gas pipework with a red valve wheel" style="left:83px;top:1982px;background:linear-gradient(180deg,#dc9a92,#d68a6e)"><span style="top:210px">PIPED GAS<br>– LPG INSTALLATION</span></div>
  <div class="project-frame" style="left:430px;top:1971px"></div>
  <div class="project-img" role="img" aria-label="Petroleum storage tanks at dusk" style="left:446px;top:1982px;background:linear-gradient(180deg,#c8663f,#e07a44)"><span style="top:210px">PETROLEUM &amp; LPG<br>TERMINALS / DEPOTS</span></div>
  <div class="project-frame" style="left:793px;top:1971px"></div>
  <div class="project-img" role="img" aria-label="Petrol station canopy at dusk" style="left:809px;top:1982px;background:linear-gradient(180deg,#7a5a78,#b8684a)"><span style="top:225px">PETROL STATIONS</span></div>
</section>

<section class="partners">
  <svg class="abs" style="left:0;top:2382px" width="1200" height="805" viewBox="0 0 1200 805">
    <rect x="0" y="0" width="1200" height="805" fill="var(--grey-bg)"/>
    <polygon points="0,0 1200,0 1200,5 600,55 0,5" fill="#fff"/>
    <polygon points="0,0 600,50 1200,0 1200,10 600,86 0,10" fill="var(--orange)"/>
    <polygon points="0,585 600,500 1200,585 1200,805 0,805" fill="#fff"/>
    <polygon points="0,585 600,535 1200,585 1200,595 600,565 0,595" fill="#fff"/>
    <polygon points="0,578 600,498 1200,578 1200,590 600,535 0,590" fill="var(--orange)"/>
  </svg>
  <h2 class="section-title" style="top:2544px">OUR PARTNERS</h2>
  <div class="partner" style="left:102px;background:#2f5f8a"></div>
  <div class="partner" style="left:280px;background:#3a3a3a"></div>
  <div class="partner" style="left:467px;background:#1f4f8c"></div>
  <div class="partner" style="left:639px;background:#2d8ad0"></div>
  <div class="partner" style="left:812px;background:#3b3b3b"></div>
  <div class="partner" style="left:986px;background:#f08a2a"></div>
</section>

<footer>
  <div class="brand abs" style="left:510px;top:3000px"><span class="brand-dot"></span><span>Kovadrel<br>Limited</span></div>
  <p class="abs" style="left:180px;top:3104px;width:840px;text-align:center;font-size:15px;line-height:29px;color:var(--muted)">Lorem ipsum dolor sit amet, consectetur adipiscing elit, sed do eiusmod tempor incididunt ut labore et dolore magna aliqua. Quis ipsum suspendisse ultrices gravida.</p>

  <div class="contact">
    <div class="c-icon" style="left:85px;top:46px"><svg width="16" height="20" viewBox="0 0 16 20"><path d="M8 1a6 6 0 0 0-6 6c0 5 6 12 6 12s6-7 6-12a6 6 0 0 0-6-6z" fill="#fff"/><circle cx="8" cy="7" r="2.3" fill="var(--orange)"/></svg></div>
    <div class="c-text" style="left:134px;top:39px">Kovadrel Limited<br>Larkfield Park, Ridge Road,<br>Nairobi</div>
    <div class="c-icon" style="left:388px"><svg width="18" height="18" viewBox="0 0 18 18"><path d="M4 1l3 4-2 2c1 2 3 4 5 5l2-2 4 3-2 3C8 16 2 10 1 4z" fill="#fff"/></svg></div>
    <div class="c-text" style="left:441px;top:53px">+254 700 418 362<br>+254 711 503 947</div>
    <div class="c-icon" style="left:631px"><svg width="18" height="14" viewBox="0 0 18 14"><rect x="1" y="1" width="16" height="12" fill="#fff"/><path d="M1 1l8 7 8-7" stroke="var(--orange)" stroke-width="1.5" fill="none"/></svg></div>
    <div class="c-text" style="left:683px;top:67px">info@kovadrel.example</div>
    <div class="c-icon" style="left:897px;top:46px"><svg width="18" height="18" viewBox="0 0 18 18"><circle cx="9" cy="9" r="7" stroke="#fff" stroke-width="1.8" fill="none"/><path d="M9 5v4l3 2" stroke="#fff" stroke-width="1.8" fill="none"/></svg></div>
    <div class="c-text" style="left:950px;top:39px">Mon– Fri &nbsp;- &nbsp;8:00 – 5:00<br>Sat &nbsp;&nbsp;&nbsp;- &nbsp;&nbsp;&nbsp;9:00 – 12:00<br>Sun &nbsp;&nbsp;- &nbsp;&nbsp;&nbsp;Closed</div>
  </div>

  <nav class="foot-nav"><span>Home</span><span>About Us</span><span>Our Clients</span><span>Our Partners</span><span>Where We Operate</span><span>Contact Us</span></nav>
  <div class="rule"></div>
  <p class="copy">©Copyrights 2023 Kovadrel Limited | All Rights Reserved</p>
</footer>

</body>
</html>
```